Brightbay Orthodontics business card design

Need a business card design that reflects our re-branding (orthodontic office - braces) and a new partnership with a pediatric dental office. We would like to include "for adults and children" on the card as well so adults know they are welcome to get their braces here as well. Office design is modern and would like business card to reflect a modern type look. Here's the text we would like to be included on the card:

Darren Wolcott, DDS, MSD
5214 West Linden Avenue, Suite 204
Mansfield, TX 76991
555-418-2637
www.brightbayortho.example
info@brightbayortho.example

Can we add the following to the existing designs? Darren Wolcott, DDS, MSD 5214 West Linden Avenue, Suite 204 Mansfield, TX 76991 555-418-2637

Does anyone have any more vertical designs available? Thanks!

Dental

```html
<!DOCTYPE html>
<html lang="en">
<head>
<meta charset="utf-8">
<title>Brightbay Orthodontics – Business Card</title>
<link rel="stylesheet" href="https://fonts.googleapis.com/css2?family=Open+Sans:wght@400;600;700&display=swap">
<style>
  :root {
    --backdrop: #8a8780;
    --card: #f6f6f6;
    --card-shade: #e4e4e4;
    --ink: #2b2b2b;
    --muted: #555555;
    --magenta: #d6127f;
    --black: #1c1c1c;
    --yellow: #f1e21a;
    --blue: #1e8bc3;
    --green: #6cb33f;
    --orange: #ee8a1d;
  }
  * { box-sizing: border-box; margin: 0; padding: 0; }
  html, body { width: 1200px; height: 871px; overflow: hidden; }
  body {
    background: var(--backdrop);
    font-family: "Open Sans", Arial, sans-serif;
    position: relative;
  }
  .card {
    position: absolute;
    background: linear-gradient(160deg, #ffffff 0%, var(--card) 55%, var(--card-shade) 100%);
    box-shadow: 0 14px 30px rgba(0,0,0,.45);
  }

  /* Front: landscape */
  .card--front { left: 60px; top: 255px; width: 610px; height: 350px; }
  .brand {
    position: absolute;
    display: flex; align-items: center; gap: 12px;
    color: var(--ink); font-weight: 700;
  }
  .brand__dot { border-radius: 50%; background: var(--magenta); flex: none; }
  .card--front .brand { left: 0; right: 0; top: 70px; justify-content: center; font-size: 34px; }
  .card--front .brand__dot { width: 26px; height: 26px; }
  .band {
    position: absolute; height: 36px;
    color: #fff; font-size: 19px; letter-spacing: 1.5px;
    display: flex; align-items: center; justify-content: center;
  }
  .band--children { left: 0; top: 178px; width: 340px; background: var(--magenta); }
  .band--adults { right: 0; top: 214px; width: 340px; background: var(--black); }

  /* Back: portrait */
  .card--back { left: 760px; top: 130px; width: 350px; height: 610px; }
  .card--back .brand { left: 30px; top: 34px; font-size: 20px; gap: 9px; }
  .card--back .brand__dot { width: 16px; height: 16px; }
  .colour-strip {
    position: absolute; left: 0; bottom: 0; width: 24px;
    display: flex; flex-direction: column;
  }
  .colour-strip span { display: block; width: 24px; height: 46px; }
  .details {
    position: absolute; left: 58px; right: 20px; bottom: 40px;
    color: var(--muted);
  }
  .details__name { color: var(--ink); font-weight: 700; font-size: 19px; margin-bottom: 22px; }
  .details__address { font-size: 13.5px; line-height: 1.55; margin-bottom: 18px; }
  .contact { list-style: none; font-size: 13.5px; }
  .contact li { display: flex; align-items: center; gap: 9px; margin-bottom: 8px; }
  .contact svg { width: 16px; height: 16px; flex: none; }
</style>
</head>
<body>

<section class="card card--front" aria-label="Card front">
  <div class="brand"><span class="brand__dot"></span>Brightbay Orthodontics</div>
  <div class="band band--children">FOR CHILDREN</div>
  <div class="band band--adults">&amp; ADULTS</div>
</section>

<section class="card card--back" aria-label="Card back">
  <div class="brand"><span class="brand__dot"></span>Brightbay Orthodontics</div>

  <div class="details">
    <p class="details__name">Darren Wolcott, DDS, MSD</p>
    <p class="details__address">5214 West Linden Avenue, Suite 204<br>Mansfield, TX 76991</p>
    <ul class="contact">
      <li>
        <svg viewBox="0 0 16 16" aria-hidden="true"><circle cx="8" cy="8" r="8" fill="var(--green)"/><path d="M5 4.5c.6-.4 1.1-.2 1.4.4l.5 1.1c.2.4 0 .8-.3 1l-.4.3c.4.9 1 1.5 1.9 1.9l.3-.4c.3-.3.7-.4 1-.2l1.1.5c.6.3.8.8.4 1.4-.5.8-1.4 1.1-2.4.7-2-.8-3.4-2.2-4.1-4.1-.3-1 0-1.9.6-2.6z" fill="#fff"/></svg>
        555-418-2637
      </li>
      <li>
        <svg viewBox="0 0 16 16" aria-hidden="true"><circle cx="8" cy="8" r="8" fill="var(--green)"/><rect x="4" y="5" width="8" height="6" rx="1" fill="#fff"/><path d="M4.3 5.4 8 8.3l3.7-2.9" fill="none" stroke="var(--green)" stroke-width="1"/></svg>
        info@brightbayortho.example
      </li>
      <li>
        <svg viewBox="0 0 16 16" aria-hidden="true"><circle cx="8" cy="8" r="8" fill="var(--green)"/><circle cx="8" cy="8" r="4" fill="none" stroke="#fff" stroke-width="1.1"/><path d="M4 8h8M8 4c-1.6 2.4-1.6 5.6 0 8M8 4c1.6 2.4 1.6 5.6 0 8" fill="none" stroke="#fff" stroke-width="1"/></svg>
        www.brightbayortho.example
      </li>
    </ul>
  </div>

  <div class="colour-strip" aria-hidden="true">
    <span style="background:var(--yellow)"></span>
    <span style="background:var(--blue)"></span>
    <span style="background:var(--magenta)"></span>
    <span style="background:var(--green)"></span>
    <span style="background:var(--orange)"></span>
  </div>
</section>

</body>
</html>
```